Maple Grove Schools | brand new stationery!

We need stationery design with our new logo! Our company updated it's name and image and we like to incorporate the new one on our stationery, business cards and email signature. We are looking for fresh, new ideas!
Industry: Childcare, Elementary and Middle School
Company Name: Maple Grove Schools
Tagline: Bright Futures Start Here
Main colors: Blue, white and a little yellow
Star shape is something new for us! Do you see a way to incorporate it as a design element?

```html
<!DOCTYPE html>
<html lang="en">
<head>
<meta charset="utf-8">
<title>Maple Grove Schools — Business Card</title>
<link rel="stylesheet" href="https://fonts.googleapis.com/css2?family=Poppins:wght@400;700&family=Montserrat:wght@400;500&family=Open+Sans:wght@400&display=swap">
<style>
  :root {
    --navy: #0b1a6e;
    --yellow: #f5b800;
    --ink: #1c1c1c;
    --grey-text: #555a66;
    --white: #ffffff;
    --stage: #2a2b2e;
  }
  * { margin: 0; padding: 0; box-sizing: border-box; }
  html, body { width: 1200px; height: 874px; overflow: hidden; background: var(--stage); }
  .canvas { position: relative; width: 1200px; height: 874px; }

  .card { position: absolute; overflow: hidden; box-shadow: 0 18px 40px rgba(0,0,0,.45); }

  /* Back of card */
  .card-back {
    left: 400px; top: 40px; width: 640px; height: 366px;
    background: var(--navy);
  }
  .card-back .brand {
    position: absolute; left: 0; right: 0; top: 128px;
    text-align: center; color: var(--white);
    font: 700 40px/1.1 "Poppins", sans-serif;
  }
  .card-back .brand-dot {
    display: block; width: 18px; height: 18px; border-radius: 50%;
    background: var(--yellow); margin: 0 auto 18px;
  }
  .card-back .web {
    position: absolute; left: 0; right: 0; bottom: 34px; text-align: center;
    color: var(--white); font: 400 15px/1 "Montserrat", sans-serif; letter-spacing: 4px;
  }

  /* Front of card */
  .card-front {
    left: 160px; top: 430px; width: 720px; height: 411px;
    background: var(--white);
  }
  .front-brand {
    position: absolute; left: 40px; top: 128px; width: 300px; text-align: center;
  }
  .front-brand .brand-dot {
    display: block; width: 20px; height: 20px; border-radius: 50%;
    background: var(--navy); margin: 0 auto 14px;
  }
  .front-brand .brand-name {
    color: var(--ink); font: 700 36px/1.08 "Poppins", sans-serif;
  }
  .divider {
    position: absolute; left: 372px; top: 112px; width: 1px; height: 186px; background: #333;
  }
  .contact { position: absolute; left: 398px; top: 118px; width: 310px; }
  .contact .person {
    color: var(--navy); font: 500 24px/1 "Montserrat", sans-serif; letter-spacing: 1px;
    text-transform: uppercase;
  }
  .contact .role { color: var(--yellow); font: 400 15px/1.2 "Open Sans", sans-serif; margin: 3px 0 10px; }
  .contact-list { list-style: none; }
  .contact-list li {
    display: flex; align-items: flex-start; gap: 9px; margin-bottom: 2px;
    color: var(--grey-text); font: 400 14px/1.3 "Open Sans", sans-serif;
  }
  .contact-list svg { flex: 0 0 12px; width: 12px; height: 12px; margin-top: 3px; fill: var(--navy); }

  .web-band {
    position: absolute; left: 0; right: 0; top: 318px; height: 36px; background: var(--navy);
    color: var(--white); font: 400 16px/36px "Montserrat", sans-serif; letter-spacing: 3px;
    padding-left: 90px;
  }
  .band-star {
    position: absolute; left: 532px; top: 300px; width: 42px; height: 42px; fill: var(--yellow);
  }
</style>
</head>
<body>
<main class="canvas">

  <section class="card card-back" aria-label="Business card back">
    <div class="brand"><span class="brand-dot"></span>Maple Grove Schools</div>
    <div class="web">WWW.MAPLEGROVESCHOOLS.COM</div>
  </section>

  <section class="card card-front" aria-label="Business card front">
    <div class="front-brand">
      <span class="brand-dot"></span>
      <div class="brand-name">Maple Grove<br>Schools</div>
    </div>

    <div class="divider"></div>

    <div class="contact">
      <div class="person">Daniel Harper</div>
      <div class="role">President</div>
      <ul class="contact-list">
        <li>
          <svg viewBox="0 0 12 12"><path d="M6 0a4 4 0 0 0-4 4c0 3 4 8 4 8s4-5 4-8a4 4 0 0 0-4-4zm0 5.6A1.6 1.6 0 1 1 6 2.4a1.6 1.6 0 0 1 0 3.2z"/></svg>
          <span>2146 Willow Bend Road<br>Juneau, Alaska 34810</span>
        </li>
        <li>
          <svg viewBox="0 0 12 12"><path d="M2.4 0 4.6 2.6 3.4 4.2a7 7 0 0 0 4.4 4.4l1.6-1.2L12 9.6 10.6 12C5 12 0 7 0 1.4z"/></svg>
          <span>555-214-7730</span>
        </li>
        <li>
          <svg viewBox="0 0 12 12"><path d="M3 0h6v12H3zM4 1v8.5h4V1zm2 9.2a.7.7 0 1 0 0 1.4.7.7 0 0 0 0-1.4z"/></svg>
          <span>555-608-1942</span>
        </li>
        <li>
          <svg viewBox="0 0 12 12"><path d="M3 0h6v3H3zM1 4h10v5H9v3H3V9H1zm3 4v3h4V8z"/></svg>
          <span>555-390-4415</span>
        </li>
        <li>
          <svg viewBox="0 0 12 12"><path d="M0 2h12v8H0zm1 1v.4l5 3.3 5-3.3V3zm0 1.6V9h10V4.6L6 8z"/></svg>
          <span>hello@maplegroveschools.com</span>
        </li>
      </ul>
    </div>

    <div class="web-band">WWW.MAPLEGROVESCHOOLS.COM</div>
    <svg class="band-star" viewBox="0 0 24 24" aria-hidden="true"><path d="M12 1.5l3.1 6.6 7.2.9-5.3 5 1.4 7.1L12 17.6l-6.4 3.5L7 14l-5.3-5 7.2-.9z"/></svg>
  </section>

</main>
</body>
</html>
```